13 Varno - new website design project

Our company Varno Electrical is developing a new lead generation website focused on Electrical, LED Lighting and Solar Power. We need a high converting website.

Example of our current website is www.varnoelectrical-example.com.au You can take content from this website for this new design. Our colours are red, black and white. For our new website we would like to promote Varno, Spark Every Day. Please listen to the jingle.

The below link is the company jingle that we have developed.
http://www.tunecraftdemo.com.au/vrn-tc-v1/

The key for this brief is to generate leads for Electrical, LED Lighting (for commercial) and Solar Power & Storage.

Target Market(s)

Business owners in Melbourne Victoria

Number of Pages Required

4 page

Colors
ec1f27
ffffff

Requirements
Must have
• This page must be clean, be in line with company branding and a high converting lead website.

```html
<!DOCTYPE html>
<html lang="en">
<head>
<meta charset="utf-8">
<title>Varno Electrical</title>
<link rel="stylesheet" href="https://fonts.googleapis.com/css2?family=Roboto:wght@300;400;700&family=Roboto+Condensed:wght@300;400;700&display=swap">
<style>
  :root {
    --brand-red: #ec1f27;
    --white: #ffffff;
    --ink: #1c1c1c;
    --body-text: #333333;
    --panel-grey: #f4f5f7;
    --hero-top: #4a6aa6;
    --hero-bottom: #2b3358;
    --nav-rule: rgba(255,255,255,0.45);
    --badge-fill: rgba(255,255,255,0.14);
  }
  * { margin: 0; padding: 0; box-sizing: border-box; }
  html, body { width: 1200px; height: 676px; overflow: hidden; background: var(--white); }
  body { font-family: "Roboto", Arial, sans-serif; position: relative; }

  .hero { position: absolute; left: 0; top: 0; width: 1200px; height: 478px; overflow: hidden; }
  .hero-photo { position: absolute; inset: 0; background: linear-gradient(180deg, var(--hero-top), var(--hero-bottom)); }

  .site-header { position: absolute; left: 0; top: 0; width: 100%; height: 72px; border-bottom: 1px solid var(--nav-rule); }
  .brand { position: absolute; left: 48px; top: 20px; display: flex; align-items: center; gap: 8px;
           font-family: "Roboto Condensed", Arial, sans-serif; font-weight: 700; font-size: 30px;
           color: var(--white); letter-spacing: 1px; }
  .brand-dot { width: 14px; height: 14px; border-radius: 50%; background: var(--brand-red); }
  .main-nav { position: absolute; left: 330px; top: 28px; display: flex; gap: 34px; list-style: none; }
  .main-nav li { color: var(--white); font-size: 14px; font-weight: 400; letter-spacing: 0.2px; }
  .call-button { position: absolute; right: 56px; top: 22px; background: var(--white); color: var(--ink);
                 font-family: "Roboto Condensed", Arial, sans-serif; font-size: 13px; padding: 7px 14px;
                 border-radius: 16px; }

  .hero-badge { position: absolute; left: 428px; top: 120px; width: 270px; height: 270px; border-radius: 50%;
                background: var(--badge-fill); display: flex; flex-direction: column; align-items: center;
                justify-content: center; color: var(--white); text-transform: uppercase; text-align: center;
                line-height: 1.05; }
  .hero-badge .line-light { font-weight: 300; font-size: 34px; letter-spacing: 1px; }
  .hero-badge .line-bold { font-weight: 700; font-size: 44px; }

  .welcome { position: absolute; left: 0; top: 478px; width: 100%; height: 112px; background: var(--white); text-align: center; }
  .section-title { font-family: "Roboto Condensed", Arial, sans-serif; font-weight: 700; font-size: 23px; color: var(--ink); }
  .section-title span { color: var(--brand-red); }
  .dashed-rule { width: 1000px; margin: 10px auto 0; height: 0; border-top: 1px dashed var(--brand-red); }
  .welcome .section-title { padding-top: 10px; }
  .welcome p { width: 960px; margin: 14px auto 0; font-family: "Roboto Condensed", Arial, sans-serif; font-size: 13px;
               font-weight: 400; line-height: 18px; color: var(--body-text); }

  .services { position: absolute; left: 0; top: 590px; width: 100%; height: 86px; background: var(--panel-grey); text-align: center; }
  .services .section-title { padding-top: 20px; }
</style>
</head>
<body>
  <section class="hero">
    <div class="hero-photo" role="img" aria-label="Hero photograph: rooftop solar panels with a city skyline beside a modern glass house lit at dusk"></div>

    <header class="site-header">
      <div class="brand"><span class="brand-dot"></span>Varno</div>
      <ul class="main-nav">
        <li>HOME</li>
        <li>ABOUT US</li>
        <li>SERVICES</li>
        <li>OUR WORK</li>
        <li>CONTACT</li>
      </ul>
      <div class="call-button">Call: 13 47 90</div>
    </header>

    <div class="hero-badge">
      <span class="line-light">Do you</span>
      <span class="line-bold">Need</span>
      <span class="line-light">A</span>
      <span class="line-light">Electrician</span>
    </div>
  </section>

  <section class="welcome">
    <h2 class="section-title">Welcome to <span>Varno Electrical</span></h2>
    <div class="dashed-rule"></div>
    <p>Varno Electrical was formed to be an expert Electricity Contracting Company providing services to all Residential and Commercial Customers. With over 10 years of experience, Varno Electrical has developed a highly-experienced team of professionals that ensure all our customer expectations are met.</p>
  </section>

  <section class="services">
    <h2 class="section-title">Our <span>Services</span></h2>
    <div class="dashed-rule"></div>
  </section>
</body>
</html>
```